Landing Page & Logo for Over 50s Guaranteed Life Cover

www.ripeyearsquote.com provides a method of comparing guaranteed life cover for consumers aged over 50. The approach we are initially looking to deploy is a simple landing page that provides the user with high level information about RipeYearsQuote and allows them to see which provider is offering the best deal by ranking providers in a table. This will compare costs / core features in the same way as shown in the attached file.

The page should incorporate a new logo design for RipeYearsQuote.com which should be similar in design to the website maplegreyhub.com.

Key elements of the landing page include:

Header (incorporating new logo and strapline e.g. "helping you find the best cover at the best price")
Introductory Text (to allow brief description of the service)
Comparison Table (to show top 10 providers - to include logos)
Table Links (allows customer to link directly from the table to the providers site)
Helpline (details of helpline number 0800 617 2948 - not actual number)
Join The Club (allows customers to sign up - using their email - to the over 50s club for more information and offers)

Other design elements welcomed to ensure the landing page is simple to understand, easy to navigate, visually appealing, focused on driving action / sales.
Updates

Target Market(s)

50 - 80

Industry/Entity Type

Insurance

Logo Text

ripeyearsquote and strapline "helping you find the best cover at the best price"

Number of Pages Required

1 page

Font styles to use
Sans Serif

Colors
a5ce39
add136
cadf82
eaf2ce
ffffff

Requirements
Nice to have
• Ideally created so content can be managed via WordPress.

```html
<!DOCTYPE html>
<html lang="en">
<head>
<meta charset="utf-8">
<title>RipeYearsQuote – Guaranteed Life Cover</title>
<link rel="stylesheet" href="https://fonts.googleapis.com/css2?family=Montserrat:wght@400;500;600;700&family=Raleway:wght@300;400;500&display=swap">
<style>
:root{
  --lime:#a5ce39;
  --lime-soft:#dce9ae;
  --lime-pale:#eaf2ce;
  --white:#ffffff;
  --orange:#ff4a00;
  --ink:#4d5150;
  --helpline-grey:#555555;
}
*{box-sizing:border-box;margin:0;padding:0}
html,body{width:1200px;height:924px;overflow:hidden}
body{font-family:"Raleway",sans-serif;color:var(--white);background:var(--white);position:relative}

.site-header{position:absolute;left:0;top:0;width:1200px;height:139px;background:var(--lime)}
.brand{position:absolute;left:86px;top:40px;display:flex;align-items:center;gap:12px}
.brand-dot{width:34px;height:34px;border-radius:50%;background:#f4c300}
.brand-name{font-family:"Raleway",sans-serif;font-weight:500;font-size:40px;line-height:44px;color:var(--white);letter-spacing:.3px}
.strapline{position:absolute;left:142px;top:96px;font-family:"Raleway",sans-serif;font-weight:400;font-size:18px;color:var(--white)}

.helpline{position:absolute;left:647px;top:49px;width:465px;height:57px}
.helpline-box{position:absolute;left:0;top:0}
.helpline-inner{position:absolute;left:47px;top:0;height:57px;display:flex;align-items:center;gap:12px}
.helpline-label{font-family:"Montserrat",sans-serif;font-size:23px;color:var(--helpline-grey);margin-left:4px}
.helpline-number{font-family:"Montserrat",sans-serif;font-size:29px;color:var(--orange);letter-spacing:.5px}

.hero{position:absolute;left:0;top:139px;width:1200px;height:515px}
.hero-photo{position:absolute;inset:0;background:linear-gradient(100deg,#b9b7b3 0%,#c7c0b8 35%,#b7a89c 60%,#9a9fa6 85%,#c9c8c4 100%)}
.hero-copy{position:absolute;left:87px;top:104px;width:500px}
.hero-title{font-family:"Montserrat",sans-serif;font-weight:700;font-size:38px;line-height:44px}
.hero-text{margin-top:10px;font-weight:300;font-size:17px;line-height:29px}
.cta{display:inline-block;margin-top:14px;width:223px;height:51px;background:var(--orange);border:1px solid #ff7a44;color:var(--white);font-family:"Raleway",sans-serif;font-weight:500;font-size:18px;line-height:49px;text-align:center;text-decoration:none}
.slider-arrow{position:absolute;top:208px;width:48px;height:48px}
.slider-arrow.prev{left:14px}
.slider-arrow.next{left:1134px}

.club{position:absolute;left:0;top:654px;width:1200px;height:194px;background:linear-gradient(110deg,var(--lime-pale) 0%,var(--lime-soft) 50%,#e3edbc 100%);text-align:center}
.club-title{margin-top:30px;font-family:"Montserrat",sans-serif;font-weight:400;font-size:29px;color:var(--ink)}
.club-sub{margin-top:8px;font-family:"Montserrat",sans-serif;font-size:16.5px;color:var(--ink)}
.signup{position:absolute;left:384px;top:116px;display:flex}
.signup-email{width:311px;height:39px;border:1px solid #e4e4e4;background:var(--white);font-family:"Montserrat",sans-serif;font-size:15px;color:#888;padding-left:13px;line-height:37px;text-align:left}
.signup-button{width:121px;height:39px;background:var(--orange);color:var(--white);font-family:"Montserrat",sans-serif;font-weight:600;font-size:15px;line-height:39px}

.site-footer{position:absolute;left:0;top:848px;width:1200px;height:76px;background:var(--lime);font-family:"Montserrat",sans-serif;font-size:13.5px}
.copyright{position:absolute;left:88px;top:29px}
.social{position:absolute;left:832px;top:22px;display:flex;align-items:center;gap:9px}
.social-label{margin-right:0}
.social-link{width:31px;height:31px;border:2px solid var(--white);border-radius:50%}
</style>
</head>
<body>
<header class="site-header">
  <div class="brand">
    <span class="brand-dot"></span>
    <span class="brand-name">RipeYearsQuote</span>
  </div>
  <p class="strapline">helping you find the best cover at the best price</p>
  <div class="helpline">
    <svg class="helpline-box" width="465" height="57" viewBox="0 0 465 57"><polygon points="0,0 465,0 455,57 12,57" fill="#fff"/></svg>
    <div class="helpline-inner">
      <svg width="36" height="36" viewBox="0 0 36 36" aria-hidden="true">
        <circle cx="18" cy="18" r="16" fill="none" stroke="#555" stroke-width="2.5"/>
        <path d="M12 10c1-1 2-1 3 0l2 3c.5 1 0 2-1 2.5-.5.5 0 2 1.5 3.5s3 2 3.5 1.5c.5-1 1.5-1.5 2.5-1l3 2c1 1 1 2 0 3l-1.5 1.5c-2 2-6 0-9.5-3.5S9.5 13.5 11 12z" fill="#555"/>
      </svg>
      <span class="helpline-label">Helpline</span>
      <span class="helpline-number">0800 617 2948</span>
    </div>
  </div>
</header>

<section class="hero">
  <div class="hero-photo" role="img" aria-label="Photo of a smiling older man with his daughter and grandson"></div>
  <div class="hero-copy">
    <h1 class="hero-title">Comparing Guaranteed<br>Life Cover</h1>
    <p class="hero-text">RipeYearsQuote has teamed up with our friends at Clearbrook to bring you high quality low cost cover from leading insurers.</p>
    <a class="cta" href="#">GET A FREE QUOTES</a>
  </div>
  <svg class="slider-arrow prev" viewBox="0 0 48 48" aria-label="Previous slide"><circle cx="24" cy="24" r="24" fill="#fff" fill-opacity=".18"/><polyline points="30,10 18,24 30,38" fill="none" stroke="#fff" stroke-width="1.5"/></svg>
  <svg class="slider-arrow next" viewBox="0 0 48 48" aria-label="Next slide"><circle cx="24" cy="24" r="24" fill="#fff" fill-opacity=".12"/><polyline points="18,10 30,24 18,38" fill="none" stroke="#fff" stroke-width="1.5"/></svg>
</section>

<section class="club">
  <h2 class="club-title">Join The Club</h2>
  <p class="club-sub">Over 50s club for more information and Offers</p>
  <div class="signup">
    <div class="signup-email">Email address</div>
    <div class="signup-button">SIGN UP</div>
  </div>
</section>

<footer class="site-footer">
  <p class="copyright">Copyrights © 2016 RipeYearsQuote. All rights reserved.</p>
  <div class="social">
    <span class="social-label">Connected Us On:</span>
    <span class="social-link" aria-label="Social link 1"></span>
    <span class="social-link" aria-label="Social link 2"></span>
    <span class="social-link" aria-label="Social link 3"></span>
    <span class="social-link" aria-label="Social link 4"></span>
  </div>
</footer>
</body>
</html>
```